BRIGHT RIVER POWER.

I'd like my business logo.
contact name: Dennis Halvorsen
phone:0438759164
email: info@brightriverpower.net.au
website: www.brightriverpower.net.au

services:
solar
battery storage
LED lighting
energy saving solutions
general electrical
I'd like the design to look professional

Target Market(s)

Everyone

Industry/Entity Type

Business

Contact Information for Business Card

as described above

Requirements
Must have
• Id like the colours and the design to work well with my logo.

```html
<!DOCTYPE html>
<html lang="en">
<head>
<meta charset="utf-8">
<title>Bright River Power – Business Card</title>
<link rel="stylesheet" href="https://fonts.googleapis.com/css2?family=Open+Sans:wght@400;600;700&display=swap">
<style>
  :root {
    --page-bg: #e9eaea;
    --card-white: #ffffff;
    --green: #4aa83a;
    --green-light: #9cc83a;
    --green-deep: #3e9d34;
    --text-grey: #4a4a4a;
    --white: #ffffff;
  }
  * { box-sizing: border-box; margin: 0; padding: 0; }
  html, body {
    width: 1105px; height: 1200px; overflow: hidden;
    background: var(--page-bg);
    font-family: "Open Sans", Arial, sans-serif;
  }
  .sheet {
    position: relative; width: 1105px; height: 1200px;
  }
  .card {
    position: absolute; left: 193px; width: 718px; height: 410px; overflow: hidden;
  }
  .card--front { top: 167px; background: var(--card-white); }
  .card--back {
    top: 623px;
    background: radial-gradient(circle at 40% 40%, var(--green-light) 0%, var(--green) 60%, var(--green-deep) 100%);
  }

  /* front */
  .name-band {
    position: absolute; left: 0; top: 55px; width: 384px; height: 115px;
    background: linear-gradient(180deg, var(--green) 0%, var(--green-light) 100%);
    display: flex; align-items: center; padding-left: 48px;
  }
  .name-band__name {
    color: var(--white); font-weight: 600; font-size: 24px; margin-top: -8px;
  }
  .brand {
    position: absolute; display: flex; align-items: center; gap: 12px;
  }
  .brand--front { left: 410px; top: 86px; }
  .brand__dot {
    width: 34px; height: 34px; border-radius: 50%; background: var(--green);
  }
  .brand__name {
    font-weight: 700; font-size: 28px; color: var(--green); letter-spacing: -0.3px;
  }
  .contacts {
    position: absolute; left: 48px; top: 284px; list-style: none;
  }
  .contacts__item {
    display: flex; align-items: center; gap: 10px;
    font-size: 17px; color: var(--text-grey); line-height: 28px;
  }
  .contacts__icon { width: 17px; height: 17px; flex: none; }

  /* back */
  .services {
    position: absolute; left: 48px; top: 108px; list-style: none;
  }
  .services__item {
    color: var(--white); font-size: 18px; line-height: 28px;
    display: flex; align-items: center; gap: 13px;
  }
  .services__item::before {
    content: ""; width: 7px; height: 7px; border-radius: 50%; background: var(--white);
  }
  .brand--back { left: 42px; top: 272px; }
  .brand--back .brand__name { color: var(--white); font-size: 40px; }
  .decor-glow {
    position: absolute; left: 330px; top: 0; width: 388px; height: 410px;
    background: radial-gradient(circle at 65% 55%, rgba(255,255,255,0.16) 0%, rgba(255,255,255,0.08) 45%, rgba(255,255,255,0) 70%);
  }
</style>
</head>
<body>
<main class="sheet">
  <section class="card card--front" aria-label="Business card front">
    <div class="name-band"><span class="name-band__name">Dennis Halvorsen</span></div>
    <div class="brand brand--front">
      <span class="brand__dot"></span>
      <span class="brand__name">Bright River Power</span>
    </div>
    <ul class="contacts">
      <li class="contacts__item">
        <svg class="contacts__icon" viewBox="0 0 24 24" aria-hidden="true"><path fill="#4aa83a" d="M6.6 10.8a15.2 15.2 0 0 0 6.6 6.6l2.2-2.2c.3-.3.7-.4 1-.2 1.1.4 2.3.6 3.6.6.6 0 1 .4 1 1V20c0 .6-.4 1-1 1A17 17 0 0 1 3 4c0-.6.4-1 1-1h3.5c.6 0 1 .4 1 1 0 1.3.2 2.5.6 3.6.1.3 0 .7-.2 1z"/></svg>
        0438759164
      </li>
      <li class="contacts__item">
        <svg class="contacts__icon" viewBox="0 0 24 24" aria-hidden="true"><rect x="2" y="5" width="20" height="14" rx="1.5" fill="#4aa83a"/><path d="M3 6.5l9 6.5 9-6.5" fill="none" stroke="#fff" stroke-width="1.6"/></svg>
        info@brightriverpower.net.au
      </li>
      <li class="contacts__item">
        <svg class="contacts__icon" viewBox="0 0 24 24" aria-hidden="true"><circle cx="12" cy="12" r="10" fill="#4aa83a"/><path d="M2 12h20M12 2c3 3 3 17 0 20M12 2c-3 3-3 17 0 20" fill="none" stroke="#fff" stroke-width="1.4"/></svg>
        brightriverpower.net.au
      </li>
    </ul>
  </section>

  <section class="card card--back" aria-label="Business card back">
    <div class="decor-glow" role="img" aria-label="Large faint brand emblem decoration"></div>
    <ul class="services">
      <li class="services__item">Solar</li>
      <li class="services__item">Battery storage</li>
      <li class="services__item">LED lighting</li>
      <li class="services__item">Energy saving solutions</li>
    </ul>
    <div class="brand brand--back">
      <span class="brand__name">Bright River Power</span>
    </div>
  </section>
</main>
</body>
</html>
```